New Website Design & Build Project - Lively Oak Dishes

I am looking for a professional clean looking website design then build of a website for my meal delivery business Lively Oak Dishes. I already have the domain - www.livelyoakdishes.com.au and I will upload brief for the design and layout of the website.

I have a dropbox full of photos, designs, videos and existing graphic design work that I can share with the designers. This can be provided upon designer request.

I am looking to build this site in WORDPRESS and I would like to build the site using the Velmora Page Composer - https://velmoraskins.example/

Target Market(s)

Kids from 2-16 , Teenagers - 16 - 19, Adults - 19 - 80 + - We Cater For Everyone

Industry/Entity Type

Health And Wellness

Coding

Coded - Design and coding required

Number of Pages Required

5+ page

Colors
33b8a4
abd037
ec1f27
fbee3f
3276b5

Requirements
Must have
• Must incorporate the included Lively Oak Dishes & LOD Logo
Must incorporate designs of packaging into website design.
Must keep text styles consistant throughout design
Must be mobile, tablet and desktop view responsive on all devices.
Must be built in Wordpress
The coder must have experience with velmora skins, velmora page composer, velmora prospects and also be very experienced with setting up products using Quillo Storefront plug in-
https://quillostorefront.example/
I want to integrate Postwren - https://dealbarn.example/postwren/ into site as well
Nice to have
• All of the above
Should not have
• No dark colours

```html
<!DOCTYPE html>
<html lang="en">
<head>
<meta charset="utf-8">
<title>Lively Oak Dishes</title>
<link rel="stylesheet" href="https://fonts.googleapis.com/css2?family=Rubik:wght@500;700&family=Open+Sans:wght@400;600;700&family=Roboto+Slab:wght@700&display=swap">
<style>
:root{
  --teal:#33b8a4;
  --green:#abd037;
  --red:#ec1f27;
  --rose:#d42a3c;
  --yellow:#fbee3f;
  --blue:#3276b5;
  --ink:#1d1d1d;
  --grey-bg:#e8e8e8;
  --soft-bg:#f1f1f1;
  --white:#ffffff;
}
*{margin:0;padding:0;box-sizing:border-box}
html,body{width:1200px;height:3528px;overflow:hidden}
body{position:relative;font-family:"Open Sans",Arial,sans-serif;color:var(--ink);background:var(--white)}
.abs{position:absolute}
.heading{font-family:"Rubik",Arial,sans-serif;font-weight:700;text-transform:uppercase}
.btn{position:absolute;display:flex;align-items:center;justify-content:center;font-family:"Rubik",Arial,sans-serif;font-weight:500;text-transform:uppercase;color:var(--white);letter-spacing:.5px}
.btn-green{background:var(--green)}
.rule{position:absolute;height:4px}

/* hero */
.hero{position:absolute;left:0;top:0;width:1200px;height:733px;background:linear-gradient(135deg,#3a2418 0%,#5a3a26 45%,#3d2517 100%)}
.hero-plate{position:absolute;left:130px;top:112px;width:560px;height:575px;border-radius:50%;background:radial-gradient(circle at 50% 50%,#6f5a4a 0%,#4b3a30 55%,#3a2a20 100%)}
.logo{position:absolute;font-family:"Rubik",Arial,sans-serif;font-weight:700;white-space:nowrap}
.logo-hero{left:133px;top:38px;font-size:30px;color:var(--white)}
.top-btn{position:absolute;top:23px;height:28px;border:2px solid var(--green);color:var(--green);font-family:"Rubik",Arial,sans-serif;font-weight:500;font-size:12px;display:flex;align-items:center;justify-content:center;text-transform:uppercase}
.nav{position:absolute;top:72px;font-family:"Rubik",Arial,sans-serif;font-weight:500;font-size:14px;color:var(--white);text-transform:uppercase}
.nav.active{color:var(--green)}
.hero-title{position:absolute;left:732px;top:252px;font-size:50px;line-height:58px;color:var(--rose)}
.hero-btn{left:736px;top:397px;width:137px;height:44px;background:var(--rose);font-size:17px}
.slide-arrow{position:absolute;top:559px;width:37px;height:36px;border:2px solid var(--white)}
.badge{position:absolute;left:171px;top:500px;width:184px;height:184px;border-radius:50%;background:var(--rose);border:5px solid #f1c9cd;color:var(--white);display:flex;flex-direction:column;align-items:center;justify-content:center;transform:rotate(-18deg);font-family:"Roboto Slab",Georgia,serif}
.badge .lbl{font-size:22px;font-weight:700}
.badge .amt{font-size:32px;font-weight:700}

/* plans */
.plans{position:absolute;left:0;top:733px;width:1200px;height:483px;background:var(--grey-bg)}
.section-title{position:absolute;left:0;width:1200px;text-align:center;font-size:28px;color:var(--ink)}
.plan{position:absolute;top:155px;width:226px;height:232px;color:var(--white);text-align:center}
.plan.g{background:var(--green)}
.plan.t{background:var(--teal)}
.plan-inner{position:absolute;inset:9px;border:1.5px solid rgba(255,255,255,.8)}
.plan-name{position:absolute;left:0;right:0;top:28px;font-family:"Rubik",Arial,sans-serif;font-size:19px;line-height:26px;font-weight:500;text-transform:uppercase}
.plan-name b{font-weight:700}
.plan-price{position:absolute;left:0;right:0;top:98px;font-family:"Roboto Slab",Georgia,serif;font-size:36px;font-weight:700}
.plan-join{position:absolute;left:68px;top:166px;width:92px;height:29px;background:var(--white);font-family:"Rubik",Arial,sans-serif;font-weight:700;font-size:13px;display:flex;align-items:center;justify-content:center}
.plan.g .plan-join{color:var(--green)}
.plan.t .plan-join{color:var(--teal)}

/* about */
.about{position:absolute;left:0;top:1216px;width:1200px;height:583px;background:var(--blue)}
.about-wood{position:absolute;left:667px;top:0;width:391px;height:583px;background:linear-gradient(180deg,#6b4a32,#4a3020)}
.about-plate{position:absolute;left:576px;top:24px;width:534px;height:534px;border-radius:50%;background:radial-gradient(circle,#d7bf84 0%,#8a6a3e 55%,#2a2a2a 62%,#c08a55 70%,#a06a3a 100%)}
.pepper{position:absolute;left:488px;top:60px;width:68px;height:68px;border-radius:50%;background:radial-gradient(circle,#6d5a4e,#2d2d2d)}
.about-title{position:absolute;left:147px;top:98px;font-size:28px;line-height:37px;color:var(--white)}
.about-text{position:absolute;left:147px;top:224px;width:345px;font-size:17px;line-height:22.5px;color:var(--white)}
.about-btn{left:149px;top:442px;width:135px;height:42px;font-size:17px}

/* menu */
.menu-card{position:absolute;top:1982px;width:287px}
.menu-img{position:absolute;left:0;top:0;width:287px;height:207px}
.menu-pack{position:absolute;left:60px;top:-29px;width:167px;height:236px;background:linear-gradient(180deg,#ffffff,#ececec);box-shadow:0 2px 6px rgba(0,0,0,.2)}
.menu-name{position:absolute;left:0;top:242px;font-family:"Rubik",Arial,sans-serif;font-weight:700;font-size:18px;text-transform:uppercase}
.menu-price{position:absolute;left:0;top:268px;font-size:23px}
.menu-btn{left:2px;top:308px;width:104px;height:29px;font-size:11.5px}
.chev{position:absolute;top:2080px}

/* smoothie */
.smoothie{position:absolute;left:0;top:2397px;width:1200px;height:555px;background:var(--soft-bg)}
.smoothie-pack{position:absolute;left:205px;top:59px;width:316px;height:448px;background:linear-gradient(180deg,#fafafa,#e4e4e4);box-shadow:0 3px 10px rgba(0,0,0,.2)}
.smoothie-title{position:absolute;left:622px;top:65px;font-size:27px;line-height:34px}
.smoothie-text{position:absolute;left:622px;width:430px;font-size:17px;line-height:23px;color:#333}
.smoothie-btn{left:623px;top:450px;width:133px;height:44px;font-size:17px}

/* subscribe */
.subscribe{position:absolute;left:0;top:2952px;width:1200px;height:308px;background:var(--blue);color:var(--white);text-align:center}
.subscribe h2{position:absolute;left:0;width:1200px;top:82px;font-size:30px}
.subscribe p{position:absolute;left:0;width:1200px;top:128px;font-size:17px}
.subscribe-btn{left:529px;top:188px;width:142px;height:42px;font-size:17px}

/* footer */
.logo-foot{left:133px;top:3316px;font-size:38px;color:var(--ink)}
.follow{position:absolute;left:290px;top:3400px;font-size:15px;color:var(--blue)}
.social{position:absolute;top:3398px;width:26px;height:26px;border-radius:50%;background:var(--blue)}
.copy{position:absolute;left:268px;top:3460px;font-size:11.5px;color:#333}
.divider{position:absolute;left:557px;top:3308px;width:1px;height:183px;background:#cfcfcf}
.f-label{position:absolute;font-size:15px;color:var(--blue)}
.f-value{position:absolute;font-size:15px;color:#222}
</style>
</head>
<body>

<!-- hero -->
<section class="hero" role="img" aria-label="Grilled beef and vegetable skewers on a slate board with cherry tomatoes, salad, spring onion and red onion rings on a dark wooden table">
  <div class="hero-plate"></div>
</section>
<div class="logo logo-hero">Lively Oak Dishes</div>
<div class="top-btn" style="left:866px;width:63px">Login</div>
<div class="top-btn" style="left:945px;width:124px">Member Sign Up</div>
<div class="nav active" style="left:689px">Home</div>
<div class="nav" style="left:753px">About Us</div>
<div class="nav" style="left:856px">Menu</div>
<div class="nav" style="left:927px">Contact Us</div>
<svg class="abs" style="left:1035px;top:66px" width="30" height="28" viewBox="0 0 30 28" aria-label="Cart">
  <path d="M1 3h5l3 14h15l3-10H8" fill="none" stroke="#fff" stroke-width="2"/>
  <circle cx="11" cy="22" r="2" fill="#fff"/><circle cx="22" cy="22" r="2" fill="#fff"/>
  <circle cx="26" cy="6" r="5" fill="var(--green)"/>
</svg>
<h1 class="heading hero-title">Bulking &amp;<br>Muscle Gain</h1>
<div class="btn hero-btn">Read More</div>
<div class="slide-arrow" style="left:747px"><svg width="33" height="32" viewBox="0 0 33 32"><path d="M19 10l-6 6 6 6" fill="none" stroke="#fff" stroke-width="2"/></svg></div>
<div class="slide-arrow" style="left:801px"><svg width="33" height="32" viewBox="0 0 33 32"><path d="M14 10l6 6-6 6" fill="none" stroke="#fff" stroke-width="2"/></svg></div>
<div class="badge"><span class="lbl">Best Price</span><span class="amt">$8.99</span></div>

<!-- plans -->
<section class="plans">
  <h2 class="heading section-title" style="top:52px">Our Plan</h2>
  <div class="rule" style="left:578px;top:97px;width:44px;background:var(--green)"></div>
  <div class="plan g" style="left:90px"><div class="plan-inner"></div>
    <div class="plan-name"><b>LOD Kids</b><br>7 Day Meal Plan</div><div class="plan-price">$35</div><div class="plan-join">JOIN NOW</div></div>
  <div class="plan t" style="left:352px"><div class="plan-inner"></div>
    <div class="plan-name"><b>LOD Adult</b><br>7 Day Meal Plan</div><div class="plan-price">$54</div><div class="plan-join">JOIN NOW</div></div>
  <div class="plan g" style="left:616px"><div class="plan-inner"></div>
    <div class="plan-name"><b>LOD Adult</b> 7 Day<br>Couples Meal Plan</div><div class="plan-price">$108</div><div class="plan-join">JOIN NOW</div></div>
  <div class="plan t" style="left:875px"><div class="plan-inner"></div>
    <div class="plan-name"><b>LOD Adult</b> 21<br><span style="font-size:16px">Meals Per Week Plan</span></div><div class="plan-price">$162</div><div class="plan-join">JOIN NOW</div></div>
</section>

<!-- about -->
<section class="about">
  <div class="about-wood" role="img" aria-label="Dark wooden table surface"></div>
  <div class="about-plate" role="img" aria-label="Chicken and vegetable skewers in a black pan on a round wooden board with fresh parsley"></div>
  <div class="pepper" role="img" aria-label="Small bowl of peppercorns"></div>
  <h2 class="heading about-title">About<br>Lively Oak Dishes</h2>
  <div class="rule" style="left:147px;top:182px;width:100px;background:var(--white)"></div>
  <p class="about-text">At Lively Oak Dishes we offer meals of excellent quality and invite you to try our delicious food.The key to our success is simple: providing quality consistent food that taste great every single time. We pride ourselves on serving our customers delicious genuine dishes like: Coffee, Healthy Meals, Salads</p>
  <div class="btn btn-green about-btn">Read More</div>
</section>

<!-- menu -->
<h2 class="heading section-title" style="top:1856px">Our Menu</h2>
<div class="rule" style="left:578px;top:1902px;width:44px;background:var(--green)"></div>
<svg class="chev" style="left:78px" width="16" height="24" viewBox="0 0 16 24"><path d="M12 3L4 12l8 9" fill="none" stroke="#aaa" stroke-width="2"/></svg>
<svg class="chev" style="left:1102px" width="16" height="24" viewBox="0 0 16 24"><path d="M4 3l8 9-8 9" fill="none" stroke="#aaa" stroke-width="2"/></svg>

<div class="menu-card" style="left:133px">
  <div class="menu-img" role="img" aria-label="Kids spaghetti meal on a table setting" style="background:linear-gradient(90deg,#c9c2b8,#e7e2da,#d35a5a)"></div>
  <div class="menu-pack" role="img" aria-label="Kids spaghetti meal package"></div>
  <div class="menu-name">Kids Meals</div>
  <div class="menu-price">$15.99</div>
  <div class="btn btn-green menu-btn">Add To Cart</div>
</div>
<div class="menu-card" style="left:458px">
  <div class="menu-img" role="img" aria-label="Glasses of cold drinks with ice in red, dark and yellow" style="background:linear-gradient(90deg,#3f9a3a,#b51e2a,#3a1e12,#e2a51a)"></div>
  <div class="menu-name">Beverages</div>
  <div class="menu-price">$25.99</div>
  <div class="btn btn-green menu-btn">Add To Cart</div>
</div>
<div class="menu-card" style="left:785px">
  <div class="menu-img" role="img" aria-label="Chicken with broccoli and sweet potato meal" style="background:linear-gradient(90deg,#3a3f33,#5a5a4a,#2e3029)"></div>
  <div class="menu-pack" role="img" aria-label="Chicken with broccoli and sweet potato meal package"></div>
  <div class="menu-name">Supplements</div>
  <div class="menu-price">$25.99</div>
  <div class="btn btn-green menu-btn">Add To Cart</div>
</div>

<!-- smoothie -->
<section class="smoothie">
  <div class="smoothie-pack" role="img" aria-label="Lemon snapper with beans, broccoli and kale meal package on marble"></div>
  <h2 class="heading smoothie-title">The Best Green Smoothie<br>To Start Your Day</h2>
  <div class="rule" style="left:622px;top:148px;width:42px;background:var(--green)"></div>
  <p class="smoothie-text" style="top:188px">The King of Green Smoothies would have to be my Superfood Green Smoothie which contains all the elements necessary for unbelievable muscle growth!!! In order to strip off the fat, add lean muscle mass &amp; to provide your body with all the best vitamins &amp; minerals try the following recipe.</p>
  <p class="smoothie-text" style="top:348px">Once you have mixed it up sit back and read on to discover why this green smoothie is going to help you achieve your goals......</p>
  <div class="btn btn-green smoothie-btn">Read More</div>
</section>

<!-- subscribe -->
<section class="subscribe">
  <h2 class="heading">Lively Oak Dishes Subscription Service</h2>
  <p>Join the Lively Oak Dishes subscription service to get the lowest prices. Cancel anytime.</p>
  <div class="btn btn-green subscribe-btn">Join Now</div>
</section>

<!-- footer -->
<footer>
  <div class="logo logo-foot">Lively Oak Dishes</div>
  <div class="follow">Follow us</div>
  <div class="social" style="left:378px"></div>
  <div class="social" style="left:413px"></div>
  <div class="social" style="left:447px"></div>
  <div class="copy">Copyright © 2020 All Rights Reserved</div>
  <div class="divider"></div>

  <svg class="abs" style="left:639px;top:3312px" width="18" height="14" viewBox="0 0 18 14"><rect x="1" y="1" width="16" height="12" fill="none" stroke="var(--green)" stroke-width="2"/><path d="M1 1l8 7 8-7" fill="none" stroke="var(--green)" stroke-width="2"/></svg>
  <div class="f-label" style="left:636px;top:3336px">E mail us</div>
  <div class="f-value" style="left:636px;top:3359px">hello@livelyoakdishes.com.au</div>

  <svg class="abs" style="left:964px;top:3310px" width="16" height="16" viewBox="0 0 16 16"><path d="M3 1l3 3-2 2c1 3 3 5 6 6l2-2 3 3-2 3C7 15 1 9 1 3z" fill="var(--green)"/></svg>
  <div class="f-label" style="left:959px;top:3336px">Call us</div>
  <div class="f-value" style="left:959px;top:3359px">0491 570 156</div>

  <svg class="abs" style="left:637px;top:3408px" width="18" height="18" viewBox="0 0 18 18"><circle cx="9" cy="9" r="7.5" fill="none" stroke="var(--green)" stroke-width="2"/><path d="M9 5v4h3" fill="none" stroke="var(--green)" stroke-width="2"/></svg>
  <div class="f-label" style="left:636px;top:3433px">Opening Hours</div>
  <div class="f-value" style="left:638px;top:3458px">Mon- Friday – 9 – 5 pm &nbsp;|&nbsp; Sat – 8 am – 12 pm</div>
</footer>

</body>
</html>
```